Financial Services Consultant needs a business card

We need a business card for a new consulting company based in Melbourne called
"Quelbrook Insights". Tagline is Measure, Monitor, Save
We would like to see business card designs that are in line with the minimal style of the website www.quelbrook-insights.example
The font I have used on the website is Proxima Nova and would like the same or similar font used on the business card with a minimal design in line with the website Two sided with "QUELBROOK INSIGHTS" MEASURE, MONITOR, SAVE on one side and name, title and contact details on the otther
Updates

Hi All, thanks for your submissions, much appreciated.

I have recently added some colour to my webiste, it is hex #3a7b74 for those that wish to use it
Thanks

Hi all

thanks very much for your design submissions I am very impressed and they are much appreciated.

Interms of general feedback please find below;

Colour: I am trying to stick to a minimal design and colour scheme for my website which is still under construction, up to 3 colours( www.quelbrook-insights.example) it is currently black and white with a small amount of blue/green but I am open to suggestion/interpretations for a consulting company.

Card: I dont mind if it has rounded edges or straight, I was thinking about using a letterpress card if possible

Detail: the detail on the card will include; Name, Title, Mobile, Personal Email, Business Email,Web,Business Address

Once again thanks for submissions

Industry/Entity Type

Business

```html
<!DOCTYPE html>
<html lang="en">
<head>
<meta charset="utf-8">
<title>Quelbrook Insights – Business Card</title>
<link rel="stylesheet" href="https://fonts.googleapis.com/css2?family=Montserrat:wght@400;500&display=swap">
<style>
  :root {
    --card-teal: #3a7b74;
    --ink-white: #ffffff;
  }
  html, body {
    margin: 0;
    padding: 0;
    width: 1200px;
    height: 758px;
    overflow: hidden;
    background: var(--card-teal);
  }
  .card {
    position: relative;
    width: 1200px;
    height: 758px;
    overflow: hidden;
    background: var(--card-teal);
    color: var(--ink-white);
    font-family: "Montserrat", sans-serif;
  }
  .brand-name {
    position: absolute;
    top: 146px;
    left: 0;
    width: 1200px;
    margin: 0;
    text-align: center;
    font-weight: 400;
    font-size: 90px;
    letter-spacing: 0;
    line-height: 1;
    white-space: nowrap;
  }
  .tagline {
    position: absolute;
    top: 313px;
    left: 0;
    width: 1200px;
    margin: 0;
    text-align: center;
    font-weight: 400;
    font-size: 22px;
    letter-spacing: 0.4px;
    line-height: 1;
  }
  .contact-block {
    position: absolute;
    top: 478px;
    left: 812px;
  }
  .person-name {
    margin: 0;
    font-weight: 400;
    font-size: 50px;
    line-height: 1;
    white-space: nowrap;
  }
  .person-title {
    margin: 8px 0 0;
    font-weight: 400;
    font-size: 29px;
    line-height: 1;
    white-space: nowrap;
  }
  .contact-list {
    list-style: none;
    margin: 14px 0 0 4px;
    padding: 0;
    font-weight: 500;
    font-size: 19px;
  }
  .contact-list li {
    line-height: 33.5px;
    white-space: nowrap;
  }
</style>
</head>
<body>
  <main class="card">
    <h1 class="brand-name">QUELBROOK INSIGHTS</h1>
    <p class="tagline">MEASURE , MONITOR , SAVE</p>
    <section class="contact-block">
      <h2 class="person-name">Elias Marrow</h2>
      <p class="person-title">Creative Manager</p>
      <ul class="contact-list">
        <li>+61-0491570156</li>
        <li>elias.marrow@mailbox.example</li>
        <li>em@quelbrook-insights.example</li>
        <li>Melbourne</li>
        <li>Australia</li>
      </ul>
    </section>
  </main>
</body>
</html>
```